Verodex business card

Business card for sustainable investment company called "Verodex". Verodex is an exchange platform selling carbon credits between buyers and sellers. Carbon Credits are an environmental commodity for reducing global carbon emissions.

the card should obviously have our logo and the theme should be sustainability/environment mixed with a trading platform.

Contact Information for Business Card

Logo, Name, Title, Phone, Email

Colors
0054AA
0677BA
7BADD7
CADEEF
E8F1F8
0094D4
00A9DD
6FCCEA
C7EBF8
E9F6FB
00AB8E
00BBA5
67D7C9
C6EFE9
E9F9F6
59FF00
82FF00
B8FF75
E3FFCB
F4FFEA

```html
<!DOCTYPE html>
<html lang="en">
<head>
<meta charset="utf-8">
<title>Verodex business card</title>
<link href="https://fonts.googleapis.com/css2?family=Roboto:wght@400;500;700&display=swap" rel="stylesheet">
<style>
  :root {
    --stage: #1c1c1e;
    --card-white: #f4f5f7;
    --ink-navy: #1d2b44;
    --mark-blue: #1a9be0;
    --blue-edge: #1f78de;
    --blue-mid: #2aa6e6;
    --cyan-core: #36d8e3;
    --white: #ffffff;
  }
  * { margin: 0; padding: 0; box-sizing: border-box; }
  html, body {
    width: 1200px; height: 750px; overflow: hidden;
    background: var(--stage);
    font-family: "Roboto", Arial, sans-serif;
  }
  .canvas {
    position: relative; width: 1200px; height: 750px;
    display: flex; align-items: center; justify-content: center; gap: 50px;
  }
  .card {
    position: relative; width: 520px; height: 297px;
    border-radius: 18px; overflow: hidden;
    box-shadow: 0 14px 30px rgba(0,0,0,.45);
  }
  .card-front {
    background: var(--card-white);
    display: flex; align-items: center; justify-content: center;
  }
  .card-back {
    background: radial-gradient(ellipse 70% 80% at 55% 48%, var(--cyan-core) 0%, var(--blue-mid) 50%, var(--blue-edge) 100%);
    color: var(--white);
  }
  .brand { display: flex; align-items: center; gap: 14px; }
  .brand-square { width: 40px; height: 40px; border-radius: 4px; background: var(--mark-blue); }
  .brand-name {
    font-weight: 500; font-size: 40px; letter-spacing: 2px;
    text-transform: uppercase; color: var(--ink-navy);
  }
  .card-back .brand {
    position: absolute; top: 62px; left: 210px; gap: 12px;
  }
  .card-back .brand-square { width: 34px; height: 34px; background: var(--white); }
  .card-back .brand-name { font-size: 34px; color: var(--white); }
  .person { position: absolute; left: 30px; top: 190px; }
  .person-name { font-size: 24px; font-weight: 700; line-height: 1; }
  .person-title { font-size: 15px; font-weight: 700; margin-top: 3px; }
  .divider {
    position: absolute; left: 30px; right: 30px; top: 240px;
    height: 1px; background: rgba(255,255,255,.8);
  }
  .contact {
    position: absolute; display: flex; align-items: center; gap: 8px;
    font-size: 15px; font-weight: 400;
  }
  .contact svg { width: 14px; height: 14px; fill: var(--white); }
  .contact-phone { left: 30px; top: 250px; }
  .contact-email { right: 30px; top: 216px; }
</style>
</head>
<body>
<main class="canvas">
  <section class="card card-front" aria-label="Card front">
    <div class="brand">
      <span class="brand-square"></span>
      <span class="brand-name">Verodex</span>
    </div>
  </section>

  <section class="card card-back" aria-label="Card back">
    <div class="brand">
      <span class="brand-square"></span>
      <span class="brand-name">Verodex</span>
    </div>
    <div class="person">
      <p class="person-name">Daniel Hart</p>
      <p class="person-title">President</p>
    </div>
    <div class="contact contact-email">
      <span>info@verodex.com</span>
      <svg viewBox="0 0 16 12" aria-hidden="true"><path d="M0 0h16v12H0z" /><path d="M0 0l8 6 8-6" fill="none" stroke="#2aa6e6" stroke-width="1.4"/></svg>
    </div>
    <div class="divider"></div>
    <div class="contact contact-phone">
      <svg viewBox="0 0 24 24" aria-hidden="true"><path d="M6.6 10.8a15.1 15.1 0 0 0 6.6 6.6l2.2-2.2a1 1 0 0 1 1-.25 11.4 11.4 0 0 0 3.6.57 1 1 0 0 1 1 1V20a1 1 0 0 1-1 1A17 17 0 0 1 3 4a1 1 0 0 1 1-1h3.5a1 1 0 0 1 1 1c0 1.25.2 2.45.57 3.57a1 1 0 0 1-.25 1z"/></svg>
      <span>(555) 0142-7789</span>
    </div>
  </section>
</main>
</body>
</html>
```